Thornbury Building Company - Card Design

I am looking to use the logo designs that you already did for me to develop a business card. I would like the card to have a black background and be double sided. I want white and green logo and text. I have attached an inspiration photo of a look that I like. I would like to use the Vertical Logo attached to take up the full front side of the card. On the back where I have my name and information, I would like to have the horizontal logo or maybe even just the image of the 'A' and trees without the text. I am open, but I am looking for something clean and simple and I want the green to really pop! Additional files can be found under Design #: 58302946

Target Market(s)

Homeowners

Industry/Entity Type

Construction

Contact Information for Business Card

Name: Marcus Thornbury, Title: Project Manager, Phone: 555.274.8136, Email: thornburybuildingcompany@mailvesta.com, address: 487 Larkspur Ln, Brackendale, OR 95033, Lic# 2468317

Colors
00AB8E
00BBA5
67D7C9
C6EFE9
E9F9F6

Requirements
Nice to have
• I would like to see the logos that I have already got from ArtLoomHub, though I am open to new ones

```html
<!DOCTYPE html>
<html lang="en">
<head>
<meta charset="utf-8">
<title>Thornbury Building Company – Business Card</title>
<link rel="stylesheet" href="https://fonts.googleapis.com/css2?family=Open+Sans:wght@400;600;700&display=swap">
<style>
  :root {
    --stage: #4a4a4a;
    --card-dark: #181818;
    --green: #6db545;
    --green-bright: #3bb54a;
    --white: #ffffff;
    --text-font: "Open Sans", Arial, sans-serif;
  }
  * { box-sizing: border-box; margin: 0; padding: 0; }
  html, body {
    width: 1200px; height: 801px; overflow: hidden;
    background: var(--stage);
    font-family: var(--text-font);
  }
  .canvas {
    position: relative; width: 1200px; height: 801px;
    display: flex; align-items: center; justify-content: center; gap: 24px;
  }
  .card {
    position: relative; width: 560px; height: 320px; overflow: hidden;
    box-shadow: 0 10px 24px rgba(0,0,0,.35);
  }
  /* Contact side */
  .card--info { background: var(--card-dark); border: 1.5px solid var(--green-bright); }
  .brand-name {
    position: absolute; left: 34px; top: 108px; width: 180px;
    color: var(--white); font-weight: 700; font-size: 21px; line-height: 1.2;
    text-transform: uppercase; letter-spacing: .5px;
  }
  .brand-name .brand-dot {
    display: inline-block; width: 14px; height: 14px; border-radius: 50%;
    background: var(--green); margin-bottom: 8px;
  }
  .divider {
    position: absolute; left: 232px; top: 58px; width: 1.5px; height: 150px;
    background: var(--green);
  }
  .contact { position: absolute; left: 254px; top: 58px; right: 16px; color: var(--white); }
  .contact__name { color: var(--green); font-weight: 700; font-size: 21px; line-height: 1.2; }
  .contact__title { font-size: 13px; margin-bottom: 18px; }
  .contact__row { display: flex; align-items: center; gap: 8px; font-size: 12.5px; line-height: 1.7; white-space: nowrap; }
  .contact__row svg { width: 12px; height: 12px; fill: var(--green); flex: none; }
  .license-band {
    position: absolute; left: 0; right: 0; bottom: 30px; height: 24px;
    background: var(--green); color: var(--white);
    font-size: 12px; line-height: 24px; padding-left: 250px;
  }
  /* Logo side */
  .card--logo { background: var(--green-bright); display: flex; align-items: center; justify-content: center; }
  .logo-ring {
    width: 230px; height: 230px; border: 4px solid var(--white); border-radius: 50%;
    display: flex; align-items: center; justify-content: center; text-align: center;
  }
  .logo-name {
    color: var(--white); font-weight: 700; font-size: 24px; line-height: 1.2;
    text-transform: uppercase; letter-spacing: .5px;
  }
</style>
</head>
<body>
<main class="canvas">
  <section class="card card--info" aria-label="Business card, contact side">
    <div class="brand-name"><span class="brand-dot"></span><br>Thornbury Building Company</div>
    <div class="divider"></div>
    <div class="contact">
      <p class="contact__name">Marcus Thornbury</p>
      <p class="contact__title">Project Manager</p>
      <p class="contact__row">
        <svg viewBox="0 0 24 24" aria-hidden="true"><path d="M6.6 10.8a15.1 15.1 0 0 0 6.6 6.6l2.2-2.2a1 1 0 0 1 1-.25 11.4 11.4 0 0 0 3.6.57 1 1 0 0 1 1 1V20a1 1 0 0 1-1 1A17 17 0 0 1 3 4a1 1 0 0 1 1-1h3.5a1 1 0 0 1 1 1c0 1.25.2 2.45.57 3.57a1 1 0 0 1-.25 1z"/></svg>
        555.274.8136
      </p>
      <p class="contact__row">
        <svg viewBox="0 0 24 24" aria-hidden="true"><path d="M2 5h20v14H2zm2 2v.5l8 5 8-5V7z"/></svg>
        thornburybuildingcompany@mailvesta.com
      </p>
      <p class="contact__row">
        <svg viewBox="0 0 24 24" aria-hidden="true"><path d="M12 2a7 7 0 0 0-7 7c0 5 7 13 7 13s7-8 7-13a7 7 0 0 0-7-7zm0 9.5A2.5 2.5 0 1 1 12 6.5a2.5 2.5 0 0 1 0 5z"/></svg>
        487 Larkspur Ln, Brackendale, OR 95033
      </p>
    </div>
    <div class="license-band">License# 2468317</div>
  </section>

  <section class="card card--logo" aria-label="Business card, logo side">
    <div class="logo-ring">
      <p class="logo-name">Thornbury<br>Building<br>Company</p>
    </div>
  </section>
</main>
</body>
</html>
```